FOOD PROCESSING KICK ASS LANDING PAGE

My client is a food processing center in Massachusetts. They help startups process and scale up their products. Here is a write up: The Eastern Ridge Kitchen Works Hub was created in 2001 to support new and growing food businesses as they navigate the path of bringing a food product to market. Our mission is to promote economic development through entrepreneurship, provide opportunities for sustaining local agriculture, and promote best practices for food producers. The ERKWH offers rental manufacturing space as well as co-packing services to food businesses in the commonwealth and beyond. We also work with local farms to make value-added products, like jams, sauces, pickles and purees. In addition to these services, our team also provides one-on-one counseling and technical assistance, supporting you with business planning, product development, regulatory compliance and more. I made a mock up and video description. Please watch video: https://clipvuebox.net/watch/q7pLmZTqNeRw

General Inspiration:
Home page with banner photo: Co-Manufacturing - Brisbury Mill
https://www.pantrygrovemills.com/contact (contact page)
https://www.ovenlarkhub.org/
https://www.calloweybrook.com
https://www.hollistane.org/
https://www.spireladle.com/ (three key links on home page – kitchen, accelerator, on demand)
Business Services — Kettle Bay Hall: https://www.kettlebayhall.com/business-services

Here is the page we are redesigning and see list of vendors below: https://www.pwtgb.org/food-processing-center/

Only send landing page desktop view

Target Market(s)

Entrprenures

Industry/Entity Type

Food manufacturing

Number of Pages Required

1 page

Font styles to use
Sans Serif

Requirements
Must have
• Clean design that look amazing on mobile
Nice to have
• See mockup
Should not have
• See mockup

```html
<!DOCTYPE html>
<html lang="en">
<head>
<meta charset="utf-8">
<title>Eastern Ridge Kitchen Works Hub</title>
<link href="https://fonts.googleapis.com/css2?family=Figtree:wght@400;500;600;700;800;900&display=swap" rel="stylesheet">
<style>
:root{
  --orange:#d2602a;
  --orange-dark:#b9521f;
  --brown:#7e4428;
  --peach:#f6e5dc;
  --cream:#fcf6f2;
  --slate:#4b6a7b;
  --ink:#2d2d2d;
  --muted:#6b6b6b;
  --footer:#3a3a3a;
  --white:#ffffff;
}
*{box-sizing:border-box;margin:0;padding:0}
html,body{width:1200px;height:4733px;overflow:hidden}
body{font-family:'Figtree',sans-serif;color:var(--ink);background:var(--peach);position:relative}
.abs{position:absolute}
a{color:inherit;text-decoration:none}

/* header */
.site-header{position:absolute;top:0;left:0;width:1200px;height:75px;background:var(--white)}
.brand{left:124px;top:7px;width:62px;height:62px;border-radius:50%;background:var(--orange);color:var(--white);font-weight:800;font-size:12px;display:flex;align-items:center;justify-content:center}
.main-nav{left:380px;top:30px;display:flex;gap:20px;font-size:11px;font-weight:700;text-transform:uppercase;letter-spacing:.2px}
.socials{display:flex;gap:8px}
.socials span{width:22px;height:22px;border-radius:50%;background:var(--orange);display:block}
.site-header .socials{position:absolute;left:925px;top:26px}

/* hero */
.hero{position:absolute;top:75px;left:0;width:1200px;height:614px;background:linear-gradient(135deg,#c9c4bd 0%,#b4aca4 35%,#8f7a6c 60%,#d8d3cd 100%)}
.hero-title{left:285px;top:261px;width:628px;height:243px;background:rgba(160,62,18,.88);color:var(--white);font-weight:800;font-size:57px;line-height:66px;text-align:center;display:flex;align-items:center;justify-content:center;text-transform:uppercase}
.hero-card{left:285px;top:619px;width:628px;height:213px;background:var(--white);border-radius:6px;box-shadow:0 6px 20px rgba(0,0,0,.08);text-align:center;font-size:19px;font-weight:600;line-height:30px;padding:58px 100px 0}
.seal{left:553px;top:561px;width:92px;height:92px;border-radius:50%;background:var(--white);box-shadow:0 2px 6px rgba(0,0,0,.15);color:var(--orange);font-weight:800;font-size:15px;display:flex;align-items:center;justify-content:center}

/* text blocks */
.sec-title{font-size:34px;font-weight:800;color:var(--orange)}
.sec-lead{font-size:14px;font-weight:700;line-height:22px}
.sec-copy{font-size:10.5px;line-height:22.5px}
.sec-copy .link{color:var(--orange)}

/* prototype */
.proto-text{left:125px;top:940px;width:350px}
.proto-text .sec-lead{margin-top:28px}
.proto-text .sec-copy{margin-top:18px}
.proto-note{font-size:10.5px;font-weight:700;margin-top:24px}
.btn-outline{display:flex;align-items:center;justify-content:center;text-align:center;margin-top:16px;width:301px;height:56px;background:var(--white);border-radius:6px;color:var(--orange);font-size:13px;font-weight:600;line-height:18px}
.video{left:526px;top:922px;width:549px;height:385px;border-radius:4px;background:linear-gradient(160deg,#a9b2b9 0%,#c7c2b8 40%,#8d8a83 75%,#5f5c57 100%)}
.play{left:250px;top:168px;width:48px;height:48px;border-radius:50%;background:var(--white);display:flex;align-items:center;justify-content:center}

/* split bands */
.band{position:absolute;left:0;width:1200px;height:531px;display:flex}
.photo{width:601px;height:100%}
.panel{width:599px;height:100%;position:relative;color:var(--white)}
.panel .sec-title{color:var(--white)}
.panel-inner{position:absolute;width:356px}
.panel .sec-copy{margin-top:20px}
.accordion{background:var(--slate);padding:0 14px;margin-top:42px}
.accordion div{height:38.5px;display:flex;align-items:center;justify-content:space-between;font-size:13px;font-weight:600;border-bottom:1px solid rgba(255,255,255,.55)}
.accordion div:last-child{border-bottom:0}
.accordion svg{width:14px;height:14px}
.contact-box{margin-top:18px;background:var(--white);height:49px;color:var(--ink);font-size:10px;font-weight:600;text-align:center;line-height:15px;padding-top:10px}
.contact-box span{color:var(--orange)}

/* about */
.about{left:0;top:2540px;width:1200px;text-align:center}
.about .sec-copy{width:550px;margin:26px auto 0;color:var(--ink)}
.team-title{font-size:26px;font-weight:600;margin-top:60px}
.team{left:366px;top:2900px;display:grid;grid-template-columns:repeat(3,149px);gap:13px 11px}
.member{background:var(--white);height:69px;border-radius:3px;padding:12px 0 0 19px}
.member b{display:block;font-size:13px;font-weight:600}
.member small{display:block;font-size:9px;color:var(--muted);line-height:13px;margin-top:4px}

/* entrepreneurs */
.makers{position:absolute;left:0;top:3243px;width:1200px;height:1103px;background:var(--cream)}
.makers-title{position:absolute;top:116px;width:1200px;text-align:center;font-size:32px;font-weight:600}
.maker-grid{position:absolute;left:125px;top:190px;display:grid;grid-template-columns:repeat(4,222px);gap:24px 21px}
.maker{background:var(--white);height:360px;box-shadow:0 3px 10px rgba(0,0,0,.08)}
.maker-img{height:180px}
.maker-body{padding:18px 18px 0}
.maker h3{font-size:16px;font-weight:600}
.maker p{font-size:9px;line-height:14.5px;color:var(--muted);margin-top:14px;height:72px;overflow:hidden}
.maker a{display:block;margin-top:14px;font-size:9.5px;font-weight:700;color:var(--orange)}
.btn-more{position:absolute;left:504px;top:974px;width:193px;height:37px;background:var(--orange);color:var(--white);border-radius:6px;font-size:10px;font-weight:600;display:flex;align-items:center;justify-content:center}

/* footer */
.site-footer{position:absolute;left:0;top:4346px;width:1200px;height:313px;background:var(--footer);color:var(--white)}
.foot-mark{left:122px;top:69px;width:138px;height:138px;border-radius:50%;border:3px solid var(--white);display:flex;align-items:center;justify-content:center;font-weight:800;font-size:22px}
.foot-h{font-size:10px;font-weight:700;text-transform:uppercase}
.foot-contact{left:404px;top:63px;width:260px}
.foot-row{display:flex;gap:16px;font-size:10px;line-height:15px;margin-top:12px}
.foot-row svg{flex:0 0 12px;margin-top:1px}
.foot-contact .socials{margin-top:34px}
.foot-news{left:720px;top:63px;width:355px}
.foot-news p{font-size:10.5px;margin-top:26px}
.input{height:31px;background:#555;border-radius:4px;font-size:10px;color:#aaa;padding:10px 18px;margin-top:12px}
.news-row{display:flex;gap:8px}
.news-row .input{width:232px}
.btn-sub{width:115px;height:33px;margin-top:11px;background:var(--orange);border-radius:4px;font-size:11px;font-weight:700;display:flex;align-items:center;justify-content:center}
.cards{display:flex;gap:6px;margin-top:22px}
.cards span{width:36px;height:22px;background:var(--white);border-radius:3px;display:block}
.bottom-bar{position:absolute;left:0;top:4659px;width:1200px;height:74px;background:var(--peach);font-size:10px;color:var(--muted);padding:36px 125px 0}
</style>
</head>
<body>

<header class="site-header">
  <div class="abs brand">ERKWH</div>
  <nav class="abs main-nav">
    <a>Prototype</a><a>Co Packing</a><a>Value Add</a><a>About</a><a>Our Entrepreneurs</a>
  </nav>
  <div class="socials"><span></span><span></span><span></span><span></span><span></span></div>
</header>

<section class="hero" role="img" aria-label="Photo of two workers in hairnets and masks sorting blueberries in the processing kitchen"></section>
<h1 class="abs hero-title">Eastern Ridge<br>Kitchen Works Hub</h1>
<div class="abs hero-card">Promoting economic development through entrepreneurship, providing opportunities for sustaining local agriculture, and promoting best practices for food producers</div>
<div class="abs seal">ERKWH</div>

<section class="abs proto-text">
  <h2 class="sec-title">Prototype My Food</h2>
  <p class="sec-lead">Are you an entrepreneur with a stellar recipe?<br>Ready to commercial and scale?</p>
  <p class="sec-copy">Schedule a prototype with our team. We will work with you to turn your recipe into a commercial formula, select appropriate packaging, create a compliant label, and create a prototype of your product. <span class="link">Please submit an interest form to connect with our team.</span></p>
  <p class="proto-note">The ERKWH offers prototyping services from November–May.</p>
  <a class="btn-outline">Learn more about launching<br>a food business here</a>
</section>
<div class="abs video" role="img" aria-label="Video still of two staff members carrying boxes outside the facility">
  <div class="abs play"><svg width="18" height="20" viewBox="0 0 18 20"><path d="M2 1l15 9-15 9z" fill="#2d2d2d"/></svg></div>
</div>

<section class="band" style="top:1408px">
  <div class="photo" role="img" aria-label="Photo of green buckets full of fresh apples beside cardboard produce boxes" style="background:linear-gradient(135deg,#7fb043 0%,#c9a070 40%,#b9372a 60%,#5e8f2c 100%)"></div>
  <div class="panel" style="background:linear-gradient(180deg,#cd5e27 0%,#a9552c 60%,#7e4428 100%)">
    <div class="panel-inner" style="left:74px;top:44px">
      <h2 class="sec-title">Co-Packing</h2>
      <p class="sec-lead" style="margin-top:22px">Are you an established business looking for co-packing support? We can help!</p>
      <p class="sec-copy">The ERKWH specializes in hot pack and hold processing for shelf-stable prepared and acidified foods. Additionally, we offer slow and individual-quick-freeze processing. If your food product doesn't fit into these categories, please give us a call to discuss. If it does, please submit an interest form to connect with our team.</p>
      <div class="accordion">
        <div>What to expect<svg viewBox="0 0 14 14"><path d="M7 0v14M0 7h14" stroke="#fff" stroke-width="1.4"/></svg></div>
        <div>Pricing<svg viewBox="0 0 14 14"><path d="M7 0v14M0 7h14" stroke="#fff" stroke-width="1.4"/></svg></div>
        <div>Other qualifications and services<svg viewBox="0 0 14 14"><path d="M7 0v14M0 7h14" stroke="#fff" stroke-width="1.4"/></svg></div>
      </div>
    </div>
  </div>
</section>

<section class="band" style="top:1939px">
  <div class="panel" style="width:601px;background:linear-gradient(180deg,#c95b25 0%,#a85430 55%,#7e4428 100%)">
    <div class="panel-inner" style="left:195px;top:36px">
      <h2 class="sec-title">Value-Added</h2>
      <p class="sec-lead" style="margin-top:20px">Turn your crops into value-added products!</p>
      <p class="sec-copy">The Eastern Ridge Kitchen Works Hub can turn your crops into value added products. We offer 12 recipes for products that will feature your tomatoes, peppers, cukes, root veggies, apples and more! Farmers deliver the key ingredient(s) to the Hub and the ERKWH team will process, bottle, label and pack for you. We provide bottle, lid, label and case. Farmers sell finished product at their farms stands, as part of CSA's and in the wholesale market.</p>
      <div class="contact-box">Contact Tess today to learn more<br><span>tessv@erkwh.org or 555-310-4826, ext. 104</span></div>
      <div class="accordion" style="margin-top:12px">
        <div>Value-Added Products<svg viewBox="0 0 14 14"><path d="M7 0v14M0 7h14" stroke="#fff" stroke-width="1.4"/></svg></div>
        <div>FAQ's<svg viewBox="0 0 14 14"><path d="M7 0v14M0 7h14" stroke="#fff" stroke-width="1.4"/></svg></div>
        <div>Flash Freezing Options for Farms<svg viewBox="0 0 14 14"><path d="M7 0v14M0 7h14" stroke="#fff" stroke-width="1.4"/></svg></div>
      </div>
    </div>
  </div>
  <div class="photo" style="width:599px;background:linear-gradient(135deg,#3d4a3c 0%,#6f5a4a 45%,#9a3d22 60%,#2f3a33 100%)" role="img" aria-label="Photo of a hand holding a jar of red pasta sauce outdoors"></div>
</section>

<section class="abs about">
  <h2 class="sec-title">About Us</h2>
  <p class="sec-copy">The Eastern Ridge Kitchen Works Hub was created in 2001 to support new and growing food businesses as they navigate the path of bringing a food product to market. Our mission is to promote economic development through entrepreneurship, provide opportunities for sustaining local agriculture, as well as promote best practices for food producers. The ERKWH offers rental manufacturing space as well as co-packing services to food businesses in the commonwealth and beyond. We also work with local farms to make value-added products, like jams, sauces, pickles and purees. In addition to these services, our team also provides one-on-one counseling and technical assistance, supporting you with business planning, product development, regulatory compliance, food safety and more.</p>
  <h2 class="team-title">Our Team</h2>
</section>
<div class="abs team">
  <div class="member"><b>Nora Whitcomb</b><small>Director of Operations<br>555-310-4826 ext.110</small></div>
  <div class="member"><b>Tess Varland</b><small>Food Business Manager<br>555-310-4826 ext.104</small></div>
  <div class="member"><b>Glen Marquet</b><small>Floor Supervisor</small></div>
  <div class="member"><b>Lia Fontaine</b><small>Production Team Leader</small></div>
  <div class="member"><b>Owen Castell</b><small>Operations Team Leader</small></div>
  <div class="member"><b>Hugo Brandt</b><small>Production Worker</small></div>
  <div class="member"><b>Marco Vidal</b><small>Sanitation Specialist</small></div>
  <div class="member"><b>Reid Alcott</b><small>Production Worker</small></div>
  <div class="member"><b>Tomas Reyna</b><small>Production Worker</small></div>
</div>

<section class="makers">
  <h2 class="makers-title">Meet Our Entrepreneurs</h2>
  <div class="maker-grid">
    <article class="maker"><div class="maker-img" role="img" aria-label="Product photo of a dark syrup bottle with herbs" style="background:linear-gradient(160deg,#2f3d52,#5a4a3e)"></div><div class="maker-body"><h3>Still Meadow</h3><p>Still Meadow Is A Health &amp; Wellness Brand Dedicated To Plant Remedies. Devoted Herbalists Who Study The Properties | Energies | Actions Of Plants...</p><a>Visit Still Meadow's Website</a></div></article>
    <article class="maker"><div class="maker-img" role="img" aria-label="Farm sign artwork with red tree roots" style="background:linear-gradient(160deg,#c9404a,#e9d6d4)"></div><div class="maker-body"><h3>Clover Path Farm</h3><p>Clover Path Farm Store Exists To Bring The Best Of The Local Food System To The North Valley Community. They Aim To Provide Food To...</p><a>Visit Clover Path Farm Website</a></div></article>
    <article class="maker"><div class="maker-img" role="img" aria-label="Product photo of a bottle of turmeric honey" style="background:linear-gradient(180deg,#e9e7e4,#a04d1e)"></div><div class="maker-body"><h3>Long Lane Farm</h3><p>Long Lane Farm Grows Food And Flowers With Care. They Offer Fair Pay To Their Crew And Owners, And Foster Connection Between The Community And Local Agriculture...</p><a>Visit Long Lane's Website</a></div></article>
    <article class="maker"><div class="maker-img" role="img" aria-label="Product photo of three maple syrup bottles" style="background:linear-gradient(180deg,#f2efe9,#b0581f)"></div><div class="maker-body"><h3>Birch Tap Foods</h3><p>Birch Tap Foods Produces A Line Of Flavored Maple Syrups. The Family Still Taps Their Own Trees, But Also Use Quality, Organic Maple Syrup Supplied By Neighbors...</p><a>Visit Birch Tap's Website</a></div></article>
    <article class="maker"><div class="maker-img" role="img" aria-label="Product photo of jars of barbecue sauce" style="background:linear-gradient(180deg,#eceaea,#a33124)"></div><div class="maker-body"><h3>47th Sauce</h3><p>If You're Looking To Raise The Bar On Flavor And Heat At Your Next Cookout Give 47th Sauce A Try! 47th Sauce Is Not For The Timid. The Flavor Is Deeply Rich, Bold And Smokey...</p><a>Visit Ember Belles' Website</a></div></article>
    <article class="maker"><div class="maker-img" role="img" aria-label="Product photo of a drink glass held over a dark background" style="background:linear-gradient(160deg,#2b2b2b,#d1782b)"></div><div class="maker-body"><h3>Original Wren</h3><p>Husband And Wife, Paul And Dana Holloway Realized They Had Something Special Going When Friends Kept Asking For More Bottles...</p><a>Visit Wren's Website</a></div></article>
    <article class="maker"><div class="maker-img" role="img" aria-label="Product photo of hot sauce bottles in a display box" style="background:linear-gradient(180deg,#6a7a8a,#c9a23a)"></div><div class="maker-body"><h3>Hollerin' Hot Sauce</h3><p>Hollerin' Hot Sauce Was Born On Isla Verda, A Small Island Far To The South, And Perfected On The Coast. They Make Every Effort To Keep Their Products Sustainable.</p><a>Visit Harbor Point Hollerin's Website</a></div></article>
    <article class="maker"><div class="maker-img" role="img" aria-label="Product label artwork for hot fudge" style="background:linear-gradient(180deg,#8a2e1e,#5e1f14)"></div><div class="maker-body"><h3>Dunmores</h3><p>Dunmores Homemade Hot Fudge Is Made In Small Batches From Scratch, Using The Same Recipe They've Been Ladling Onto Their Prized Ice Cream At Their...</p><a>Visit Dunmore's Website</a></div></article>
  </div>
  <a class="btn-more">Load more Entrepreneurs</a>
</section>

<footer class="site-footer">
  <div class="abs foot-mark">ERKWH</div>
  <div class="abs foot-contact">
    <div class="foot-h">Our Contact</div>
    <div class="foot-row" style="margin-top:22px"><svg width="12" height="12" viewBox="0 0 12 12"><path d="M2 1l2 0 1 3-1.5 1a6 6 0 0 0 3.5 3.5L8 7l3 1v2a1 1 0 0 1-1 1A9 9 0 0 1 1 2a1 1 0 0 1 1-1z" fill="#d2602a"/></svg>555-310-4826</div>
    <div class="foot-row"><svg width="12" height="12" viewBox="0 0 12 12"><path d="M6 0a4 4 0 0 1 4 4c0 3-4 8-4 8S2 7 2 4a4 4 0 0 1 4-4z" fill="#d2602a"/><circle cx="6" cy="4" r="1.5" fill="#3a3a3a"/></svg>118 Alder Row, Millbrook, MA 01999</div>
    <div class="foot-row"><svg width="12" height="12" viewBox="0 0 12 12"><rect x="0.5" y="2" width="11" height="8" fill="none" stroke="#d2602a"/><path d="M0.5 2l5.5 4.5L11.5 2" fill="none" stroke="#d2602a"/></svg><span><b>Nora Whitcomb</b>, noraw@erkwh.org<br><b>Tess Varland</b>, tessv@erkwh.org</span></div>
    <div class="socials"><span></span><span></span><span></span><span></span><span></span></div>
  </div>
  <div class="abs foot-news">
    <div class="foot-h">Newsletter</div>
    <p>Register here for our ERKWH Food Safety Newsletter:</p>
    <div class="input">Full Name</div>
    <div class="news-row"><div class="input">Email</div><div class="btn-sub">Subscribe</div></div>
    <div class="cards"><span></span><span></span><span></span><span></span><span></span></div>
  </div>
</footer>
<div class="bottom-bar">Copyright 2022 Eastern Ridge Kitchen Works Hub All rights reserved.</div>

</body>
</html>
```